Hurricane Damage Public Adjuster Billboard

I have created several projects with you and have several great designs. I need to format them into a Billboard for upcoming Hurricane Season. Need done in a month. Im also in process of getting an eye catching and easy to remember 800# Vanity phone number like Call 800-Stormsafe or 800- Need Fix? My included past Craft Huddle projects will give you an idea of what colors, schemes, and designs I gravitate towards. 3 past Design projects were 1) 2 Logos where I picked the 1st place and the 2nd place and 2) Index Card where I picked the winner as the Index Card and the 2nd place as a Post Card. Point is, I will pick and pay for 2 winners if they're good. This should help to sweeten the pot. Also, please look at my website for ideas that I like:

www.TheClaimKeeperGroup.com
I want people to feel that I am the best and highest. Level.

I've been getting a lot of quick half effort designs basically cut & pasting my previous projects. Please don't rush and take your time to be creative. A an example, my Biggest Competitor is Vesta Public Adjusting. Their colors are Black and Gold while mine are Blue, White, and Black with a highlight of Orange if possible. I JUST imported a picture of their BillBoard. I need mine better and BLOW AWAY THEIRS. Terms like "Don't be Victimized Twice ?, Don't let the Hurricane Ruin your Life?". "Get Fairly Paid & Move On" "Our Clients Claims are VIP?
Updates

I'm getting a lot of quick half effort ones. I'd rather you take your time and really put some thoughts and effort into it. My Biggest Competitor is Vesta Public Adjusting. They have black & gold colors, while I have Blue, Black, and white.

It needs to blow theirs away. I have imported their Billboard for comparative purposes.

Guy's,
I'll make it easier for you in what I'm looking for. Please look at the Vesta Billboard picture attached.

1) Put my "Blue Shield" to the left, replacing their logo
2) change color patterns from their (Black, Gold, White) to my color schemes of (Black, Blue, White)
3) I want to see my name where their is:

THE
Claim Keeper's Group
EXPERT & LOCAL Public Adjusters
"FOR THE POLICYHOLDER!!"

4) to the right, add the A+Rated logo and QRS+ Accredited logo, 5 Star Zorbix Rated logo, 5 Start PORCHLINE Highly Rated logo, etc..

5) the right side is where you can be creative as I will not have a picture of me there.

"20+ Years of Experience, Recovering Millions for our VIP Clients"

"Your Best, Locally-Based Private Adjuster & Advocate'
"FOR THE POLICYHOLDER!!"

"Don't be victimized Twice!!"

"Don't let the Hurricane Ruin Your Life!!"

This should really help. Also, refer to my website, maybe a couple testimonial fillers?

Thanks all,

marcus@TheClaimKeeperGroup.com

Just imported a few awards that would look great to the right side with all the other 5 Star Ratings and accolades.
This right section could be titled like zmy Website:

5 Star Reviews, Ratings & Awards:
4-5 Logos underneath?

Target Market(s)

Coastal place where a Hurricane 🌀 🌀 Hits

Industry/Entity Type

Hurricane Public Insurance Adjuster

Font styles to use
Sans Serif
Other font styles liked:
• Zurich fonts

Colors
0054AA
0677BA
7BADD7
CADEEF
E8F1F8
EE7325
F08F49
F5BC92
FAE3D3
FDF4ED

Requirements
Must have
• Use my past project logos, colors, and schemes to create eye grabbing BillBoard
Nice to have
Should not have
• Not be too busy, must be Easy to Read, Eye Catchy

```html
<!DOCTYPE html>
<html lang="en">
<head>
<meta charset="utf-8">
<title>Claim Keeper's Group Billboard</title>
<link href="https://fonts.googleapis.com/css2?family=Poppins:wght@600;700;800&family=Roboto:wght@500;700&display=swap" rel="stylesheet">
<style>
  :root {
    --ink: #0a0a0a;
    --paper: #ffffff;
    --canvas: #f1f3f5;
    --cyan: #10e4f4;
    --sky: #1ea8ee;
    --brand-blue: #0a84d6;
    --deep-blue: #0054aa;
    --link-blue: #0677ba;
    --badge-navy: #2c3a58;
  }
  * { box-sizing: border-box; margin: 0; padding: 0; }
  html, body { width: 931px; height: 1200px; overflow: hidden; background: var(--canvas); }
  .billboard {
    position: absolute; left: 30px; top: 474px; width: 871px; height: 254px;
    box-shadow: 0 18px 40px rgba(0,0,0,.35);
    font-family: 'Poppins', sans-serif;
  }
  .headline-band { position: absolute; inset: 0 0 auto 0; height: 136px; background: var(--ink); }
  .brand-mark {
    position: absolute; left: 26px; top: 36px; width: 112px;
    color: var(--sky); font-weight: 800; font-size: 19px; line-height: 1.1; text-transform: uppercase;
  }
  .headline-lead { position: absolute; left: 156px; top: 10px; color: var(--paper); font-weight: 800; font-size: 29px; line-height: 1.1; }
  .headline-main { position: absolute; left: 155px; top: 44px; color: var(--cyan); font-weight: 800; font-size: 39px; line-height: 1.1; letter-spacing: -.4px; white-space: nowrap; }
  .byline { position: absolute; left: 156px; top: 96px; display: flex; align-items: center; gap: 10px; white-space: nowrap; }
  .tagline { color: var(--paper); font-weight: 800; font-size: 20px; line-height: 1; }
  .name-pill {
    height: 30px; padding: 0 16px; border-radius: 15px;
    background: var(--sky); color: var(--ink); font-weight: 800; font-size: 18px;
    display: flex; align-items: center;
  }
  .experience-seal {
    position: absolute; left: 724px; top: 10px; width: 124px; height: 124px; border-radius: 50%;
    background: #0d1a26; border: 2px solid var(--sky);
    display: flex; flex-direction: column; align-items: center; justify-content: center;
    color: var(--paper); text-align: center;
  }
  .seal-note { font-weight: 700; font-size: 7px; line-height: 1.2; letter-spacing: .4px; }
  .seal-core {
    width: 72px; height: 72px; border-radius: 50%; background: var(--sky); margin: 3px 0;
    display: flex; flex-direction: column; align-items: center; justify-content: center; line-height: 1;
  }
  .seal-core strong { font-weight: 800; font-size: 26px; color: var(--paper); }
  .seal-core span { font-weight: 800; font-size: 8.5px; color: var(--ink); margin-top: 2px; }
  .credentials-strip {
    position: absolute; left: 0; right: 0; top: 136px; height: 48px; background: var(--paper);
    display: flex; align-items: center; padding-left: 28px;
  }
  .credentials-claim { font-weight: 700; font-size: 15px; color: var(--ink); white-space: nowrap; }
  .credentials-claim em { font-style: normal; color: var(--brand-blue); margin-left: 6px; }
  .accolades { display: flex; align-items: center; gap: 10px; margin-left: 22px; }
  .award-badge { width: 24px; height: 30px; background: var(--badge-navy); border-radius: 3px; }
  .review-name { font-family: 'Roboto', sans-serif; font-weight: 500; font-size: 14px; color: var(--link-blue); }
  .accredit-badge { width: 50px; height: 22px; background: var(--deep-blue); border-radius: 4px; }
  .neighbor-name { font-family: 'Roboto', sans-serif; font-weight: 700; font-size: 15px; color: var(--brand-blue); letter-spacing: .3px; }
  .rating-note { text-align: center; line-height: 1; }
  .rating-note strong { display: block; font-family: 'Roboto', sans-serif; font-weight: 500; font-size: 12px; color: var(--ink); }
  .rating-note span { display: block; font-family: Georgia, serif; font-size: 5.5px; color: #333; margin-top: 2px; width: 62px; }
  .contact-band {
    position: absolute; left: 0; right: 0; bottom: 0; height: 70px; background: var(--brand-blue);
    display: flex; align-items: center; padding-left: 26px; color: var(--paper);
    font-family: 'Roboto', sans-serif; font-weight: 500;
  }
  .contact-phone { display: flex; align-items: center; gap: 8px; font-size: 32px; }
  .contact-web { display: flex; align-items: center; gap: 14px; font-size: 29px; margin-left: 18px; white-space: nowrap; }
  .contact-band svg { flex: none; }
</style>
</head>
<body>
  <div class="billboard">
    <section class="headline-band">
      <div class="brand-mark">Claim Keeper's Group</div>
      <p class="headline-lead">DON'T LET THE</p>
      <h1 class="headline-main">HURRICANE RUIN YOUR LIFE?</h1>
      <div class="byline">
        <p class="tagline">THE CLAIM KEEPER'S GROUP</p>
        <div class="name-pill">MARCUS DELACROIX</div>
      </div>
      <div class="experience-seal">
        <p class="seal-note">RECOVERING<br>MILLIONS</p>
        <div class="seal-core">
          <strong>20+</strong>
          <span>YEARS OF<br>EXPERIENCE</span>
        </div>
        <p class="seal-note">FOR OUR VIP<br>CLIENTS</p>
      </div>
    </section>

    <section class="credentials-strip">
      <p class="credentials-claim">EXPERT &amp; LOCAL Public Adjusters<em>FOR THE POLICYHOLDER!!</em></p>
      <div class="accolades">
        <div class="award-badge" role="img" aria-label="2022 award badge"></div>
        <span class="review-name">Zorbix</span>
        <div class="accredit-badge" role="img" aria-label="QRS accredited business badge"></div>
        <span class="neighbor-name">PORCHLINE</span>
        <div class="rating-note">
          <strong>A+ Rating</strong>
          <span>Highest Rating For Public Insurance Adjusters</span>
        </div>
      </div>
    </section>

    <section class="contact-band">
      <div class="contact-phone">
        <svg width="24" height="24" viewBox="0 0 24 24" aria-hidden="true"><path fill="#0a0a0a" d="M6.6 10.8c1.4 2.8 3.8 5.1 6.6 6.6l2.2-2.2c.3-.3.7-.4 1-.2 1.1.4 2.3.6 3.6.6.6 0 1 .4 1 1V20c0 .6-.4 1-1 1C10.6 21 3 13.4 3 4c0-.6.4-1 1-1h3.5c.6 0 1 .4 1 1 0 1.3.2 2.5.6 3.6.1.3 0 .7-.2 1z"/></svg>
        <span>800-STORMSAFE</span>
      </div>
      <div class="contact-web">
        <svg width="22" height="22" viewBox="0 0 24 24" aria-hidden="true" fill="none" stroke="#0a0a0a" stroke-width="1.8"><circle cx="12" cy="12" r="10"/><ellipse cx="12" cy="12" rx="4.5" ry="10"/><path d="M2 12h20M4 7h16M4 17h16"/></svg>
        <span>www.TheClaimKeeperGroup.com</span>
      </div>
    </section>
  </div>
</body>
</html>
```